Fresh Dwelling Tract Guide needs a new Landing Page

I like to get a landing page or website with 2-3 pages to help target home buyers who are looking to buy homes from builders such as TW Residences, Morvik, P.L. Fennick, etc. The landing page/website to be non-cluttered and be able to explain to home buyers that there are many benefits to include me as their buyer's agent when they buy a brand new home from any builders.
I may want to incorporate a short explanation video (animated) on the landing page and then for the viewer to click on a button that will take them to another page where they can search for new homes from different builders.
Target Market(s)
Home buyers looking to buy brand new home from builders such as TW Residences, Morvik, P.L. Fennick, etc.
Industry/Entity Type
Real Estate
Number of Pages Required
2 page
Font styles to use
Requirements
Must have
- The landing page may have the explanation video at the bottom of the landing page (scrolled down) or there may be a CALL TO ACTION button that takes the viewer to the 2nd page to watch the explanation video. Once they watched the explanation video and are still interested, they can click on another CALL TO ACTION button that will take them to another website that they will be able to search for all the available new homes and register their contact information.
Should not have
- No clutters and no dark colors.

```html
<!DOCTYPE html>
<html lang="en">
<head>
<meta charset="utf-8">
<title>Parkside Home Walk</title>
<link rel="stylesheet" href="https://fonts.googleapis.com/css2?family=Lato:wght@400;700;900&display=swap">
<style>
  :root {
    --hero-base: #8e9ba7;
    --hero-soft: #b4bec7;
    --hero-glow: #cdd5dc;
    --hero-edge: #7f8c98;
    --text-light: #ffffff;
    --text-shade: rgba(40, 48, 58, 0.45);
    --accent: #e0622a;
    --brand-dot: #f0a12b;
  }
  * { margin: 0; padding: 0; box-sizing: border-box; }
  html, body { width: 1200px; height: 675px; overflow: hidden; }
  body { font-family: "Lato", Arial, sans-serif; color: var(--text-light); }
  .landing { position: relative; width: 1200px; height: 675px; overflow: hidden; }
  .hero-photo {
    position: absolute; inset: 0;
    background:
      radial-gradient(ellipse at 72% 42%, var(--hero-glow) 0%, transparent 55%),
      linear-gradient(110deg, var(--hero-soft) 0%, var(--hero-base) 45%, var(--hero-soft) 75%, var(--hero-edge) 100%);
  }
  .brand {
    position: absolute; top: 28px; left: 0; width: 1200px;
    display: flex; flex-direction: column; align-items: center;
    text-shadow: 0 1px 6px var(--text-shade);
  }
  .brand-mark { width: 44px; height: 44px; border-radius: 50%; background: var(--brand-dot); margin-bottom: 14px; }
  .brand-name {
    font-weight: 400; color: var(--text-light); text-align: center;
    font-size: 40px; line-height: 1; letter-spacing: 1px;
  }
  .brand-name span { display: block; font-size: 16px; letter-spacing: 6px; margin-top: 6px; }
  .hero-copy {
    position: absolute; top: 216px; left: 0; width: 1200px; text-align: center;
    text-shadow: 0 2px 8px var(--text-shade);
  }
  .hero-kicker { display: block; font-size: 48px; font-weight: 900; line-height: 1.05; letter-spacing: 0.5px; }
  .hero-title { display: block; font-size: 58px; font-weight: 900; line-height: 1.05; letter-spacing: 0.3px; }
  .hero-lead { font-size: 23px; font-weight: 700; margin-top: 16px; }
  .cta-search {
    display: inline-block; margin-top: 16px;
    background: var(--accent); color: var(--text-light);
    font-size: 21px; font-weight: 700; text-decoration: none; text-shadow: none;
    width: 258px; height: 54px; line-height: 54px; border-radius: 3px;
  }
  .play-video {
    display: inline-flex; align-items: center; gap: 6px; margin-top: 14px;
    color: var(--text-light); font-size: 20px; font-weight: 700; text-decoration: underline;
  }
  .site-footer {
    position: absolute; left: 75px; right: 74px; top: 624px;
    display: flex; justify-content: space-between; align-items: center;
    text-shadow: 0 1px 4px var(--text-shade);
  }
  .copyright { font-size: 13px; font-weight: 400; }
  .social-links { display: flex; gap: 16px; list-style: none; }
  .social-links a { color: var(--text-light); font-size: 13px; font-weight: 700; text-decoration: none; }
</style>
</head>
<body>
<main class="landing">
  <div class="hero-photo" role="img" aria-label="Photo of a woman at a desk browsing new home listings on a computer monitor, softly lightened"></div>

  <header class="brand">
    <div class="brand-mark"></div>
    <p class="brand-name">Parkside<span>HOME WALK</span></p>
  </header>

  <section class="hero-copy">
    <h1>
      <span class="hero-kicker">WELCOME TO</span>
      <span class="hero-title">PARKSIDE HOME WALK</span>
    </h1>
    <p class="hero-lead">Sed ut turpis vitae ipsum malesuada maximus vulputate lobortis dui.</p>
    <a class="cta-search" href="#">Search for New Homes</a><br>
    <a class="play-video" href="#">
      <svg width="17" height="17" viewBox="0 0 16 16" aria-hidden="true">
        <circle cx="8" cy="8" r="8" fill="#ffffff"/>
        <path d="M6 4.5 L11.5 8 L6 11.5 Z" fill="#7f8c98"/>
      </svg>
      Play Video
    </a>
  </section>

  <footer class="site-footer">
    <p class="copyright">Copyright © 2018, Company Name All Right reserved</p>
    <ul class="social-links">
      <li><a href="#">Social</a></li>
      <li><a href="#">Photos</a></li>
      <li><a href="#">Posts</a></li>
      <li><a href="#">Network</a></li>
      <li><a href="#">Videos</a></li>
    </ul>
  </footer>
</main>
</body>
</html>
```